Satchel & Sundial needs new business card design

I need a new business card design. I'm looking for out-of-the-box design which represents the freedom of being a location independent entrepreneur.
I offer coaching, retreats and trips.
I would like to see designs with and without the photo.
Colors I use are black (#000000), green (#25A796) and brown (#D7C38C)
Website satchelandsundial.example

Target Market(s)

location independent entrepreneurs, digital nomads, people looking to swap the 9 to 5 for a lifestyle business

Industry/Entity Type

Business

Contact Information for Business Card

Dorota Falkner
Your Lifestyle Business Coach, Retreat & Trip Leader
http://satchelandsundial.example
hello@satchelandsundial.example
Live a life you don't need a holiday from

Font styles to use
Serif
Sans Serif

Requirements
Must have
• One side should contain only the logo. I would also consider having the "Live a life you don't need a holiday from" on that side too (depending on how it looks)
• Please show both sides on the designs.

```html
<!DOCTYPE html>
<html lang="en">
<head>
<meta charset="utf-8">
<title>Satchel &amp; Sundial — Business Card</title>
<link rel="stylesheet" href="https://fonts.googleapis.com/css2?family=Open+Sans:ital,wght@0,400;0,600;1,400&display=swap">
<style>
  :root {
    --ink: #231f20;
    --teal: #25a796;
    --white: #ffffff;
    --backdrop: #dcdcdc;
    --card-w: 718px;
    --card-h: 411px;
  }
  * { box-sizing: border-box; margin: 0; padding: 0; }
  html, body {
    width: 1105px; height: 1200px; overflow: hidden;
    background: var(--backdrop);
    font-family: "Open Sans", sans-serif;
  }
  .sheet {
    position: relative; width: 1105px; height: 1200px;
  }
  .card {
    position: absolute; left: 194px;
    width: var(--card-w); height: var(--card-h);
    overflow: hidden;
    box-shadow: 0 4px 10px rgba(0,0,0,0.25);
  }
  .card--front { top: 145px; background: var(--white); }
  .card--back { top: 600px; background: var(--teal); }

  .front-shape { position: absolute; inset: 0; width: 100%; height: 100%; }

  .brand-name {
    font-weight: 600; text-transform: uppercase; letter-spacing: 1px;
    line-height: 1;
  }
  .front-brand {
    position: absolute; right: 40px; top: 92px;
    font-size: 38px; color: var(--ink);
  }
  .holder {
    position: absolute; right: 40px; top: 192px; text-align: right;
  }
  .holder-name {
    font-size: 22px; font-weight: 600; color: var(--teal);
    text-transform: uppercase; letter-spacing: 0.5px; margin-bottom: 8px;
  }
  .holder-role {
    font-size: 18.5px; color: var(--ink); line-height: 1.4;
  }
  .contacts {
    position: absolute; left: 38px; top: 328px; list-style: none;
  }
  .contact {
    display: flex; align-items: center; gap: 10px;
    font-size: 18.5px; color: var(--white); height: 28px;
  }
  .contact-icon { width: 18px; height: 18px; flex: none; }

  .back-pattern {
    position: absolute; inset: 0;
    background: linear-gradient(160deg, #2aad9c 0%, #23a492 100%);
  }
  .social {
    position: absolute; right: 22px; top: 26px; display: flex; gap: 6px;
  }
  .social-tile { width: 24px; height: 24px; background: var(--white); }
  .back-brand {
    position: absolute; left: 0; right: 0; top: 170px; text-align: center;
    font-size: 56px; color: var(--white);
  }
  .tagline {
    position: absolute; left: 0; right: 0; top: 354px; text-align: center;
    font-size: 18px; font-style: italic; color: var(--white);
  }
</style>
</head>
<body>
<main class="sheet">

  <section class="card card--front" aria-label="Card front">
    <svg class="front-shape" viewBox="0 0 718 411" preserveAspectRatio="none" aria-hidden="true">
      <rect width="718" height="411" fill="var(--ink)"/>
      <path d="M0,0 C70,210 320,352 718,340 L718,0 Z" fill="var(--teal)"/>
      <path d="M0,0 C64,202 315,340 718,330 L718,0 Z" fill="var(--white)"/>
      <path d="M0,0 C60,198 312,334 718,324 L718,0 Z" fill="var(--white)"/>
    </svg>
    <div class="brand-name front-brand">Satchel &amp; Sundial</div>
    <div class="holder">
      <p class="holder-name">Dorota Falkner</p>
      <p class="holder-role">Your Lifestyle Business Coach</p>
      <p class="holder-role">Retreat &amp; Trip Leader</p>
    </div>
    <ul class="contacts">
      <li class="contact">
        <svg class="contact-icon" viewBox="0 0 18 18" aria-hidden="true">
          <rect x="1" y="4" width="16" height="11" fill="var(--teal)"/>
          <path d="M1,4 L9,10 L17,4" fill="none" stroke="var(--ink)" stroke-width="1.3"/>
        </svg>
        hello@satchelandsundial.example
      </li>
      <li class="contact">
        <svg class="contact-icon" viewBox="0 0 18 18" aria-hidden="true">
          <circle cx="9" cy="9" r="8" fill="var(--teal)"/>
          <path d="M1,9 H17 M9,1 C5,5 5,13 9,17 M9,1 C13,5 13,13 9,17" fill="none" stroke="var(--ink)" stroke-width="1.1"/>
        </svg>
        www.satchelandsundial.example
      </li>
    </ul>
  </section>

  <section class="card card--back" aria-label="Card back">
    <div class="back-pattern" role="img" aria-label="Faint repeated brand-name pattern in a lighter teal"></div>
    <div class="social" aria-label="Social profiles">
      <span class="social-tile"></span>
      <span class="social-tile"></span>
      <span class="social-tile"></span>
    </div>
    <div class="brand-name back-brand">Satchel &amp; Sundial</div>
    <p class="tagline">Live a life you don't need a holiday from</p>
  </section>

</main>
</body>
</html>
```